Brookvane Consulting Business Card Design

Business Card Design for Brookvane Consulting. Brookvane Consulting is a boutique consultancy based in Atlanta, GA., that specializes in marketing strategy, organization planning, and leadership development. We provide solutions for small businesses and startups as well as Vantage 300 companies.

http://brookvaneconsulting.com/

Target Market(s)

We provide solutions for small businesses and startups as well as Vantage 300 companies.

Industry/Entity Type

Consulting

Contact Information for Business Card

Two sided business card with priority on contact information, logo, tag line (Clarity to Plan Better, Lead Better, Grow Better)

Colors

Designer to choose colors to be used in the design.

Requirements
Must have
• contact information, logo, tag line (Clarity to Plan Better, Lead Better, Grow Better)
• Simple no over communication.
Nice to have
• I would like to see different placements of logo and creative use of both sides of the card
Should not have
• Do not put too much information on the card.

```html
<!DOCTYPE html>
<html lang="en">
<head>
<meta charset="utf-8">
<title>Brookvane Consulting Business Card</title>
<link rel="stylesheet" href="https://fonts.googleapis.com/css2?family=Lato:wght@400;700&display=swap">
<style>
  :root {
    --page: #e9e7e4;
    --card-white: #ffffff;
    --card-black: #050505;
    --band-grey: #3a3a3a;
    --ink-dark: #2e2e2e;
    --ink-light: #ffffff;
    --ink-silver: #d6d6d6;
    --rule: #f2f2f2;
  }
  * { box-sizing: border-box; margin: 0; padding: 0; }
  html, body { width: 1200px; height: 900px; overflow: hidden; }
  body {
    background: var(--page);
    font-family: "Lato", Arial, sans-serif;
    position: relative;
  }
  .card {
    position: absolute;
    overflow: hidden;
    box-shadow: 0 6px 18px rgba(0,0,0,0.18);
  }
  .card-front { left: 178px; top: 74px; width: 588px; height: 364px; background: var(--card-white); }
  .card-back  { left: 388px; top: 505px; width: 567px; height: 352px; background: var(--card-black); }

  .front-panels { position: absolute; inset: 0; }

  .wordmark {
    position: absolute;
    left: 0; right: 0;
    display: flex;
    align-items: center;
    justify-content: center;
    gap: 14px;
    font-weight: 400;
    letter-spacing: 1px;
    white-space: nowrap;
    line-height: 1;
  }
  .wordmark-square {
    width: 22px; height: 22px;
    border: 2px solid currentColor;
  }
  .card-front .wordmark { top: 72px; font-size: 44px; color: var(--ink-dark); }
  .card-back .wordmark  { top: 162px; font-size: 44px; color: var(--ink-silver); }

  .holder {
    position: absolute;
    right: 326px; top: 256px;
    text-align: right;
    color: var(--ink-light);
  }
  .holder-name { font-weight: 700; font-size: 19px; letter-spacing: 0.3px; }
  .holder-role { font-size: 15px; margin-top: 2px; }

  .contact-list {
    position: absolute;
    left: 292px; top: 244px;
    list-style: none;
    color: var(--ink-light);
    font-size: 15px;
    line-height: 22px;
  }
  .contact-list li { display: flex; align-items: center; gap: 6px; }
  .contact-list svg { width: 11px; height: 11px; fill: var(--ink-light); flex: none; }

  .tagline {
    position: absolute;
    left: 0; right: 0; top: 321px;
    text-align: center;
    color: var(--ink-light);
    font-size: 17px;
    letter-spacing: 0.2px;
  }

  .back-url {
    position: absolute;
    left: 0; right: 0; top: 292px;
    text-align: center;
    color: var(--ink-light);
    font-weight: 700;
    font-size: 15px;
    letter-spacing: 1px;
  }
</style>
</head>
<body>

<section class="card card-front" aria-label="Business card front">
  <svg class="front-panels" viewBox="0 0 588 364" width="588" height="364" aria-hidden="true">
    <polygon points="0,216 383,216 417,180 588,180 588,364 0,364" fill="var(--card-black)"/>
    <polygon points="0,188 405,188 384,212 0,212" fill="var(--band-grey)"/>
    <polyline points="0,216 383,216 417,180 588,180" fill="none" stroke="var(--rule)" stroke-width="2"/>
  </svg>

  <div class="wordmark"><span class="wordmark-square"></span>Brookvane Consulting</div>

  <div class="holder">
    <p class="holder-name">DANIEL REYES</p>
    <p class="holder-role">Managing Director</p>
  </div>

  <ul class="contact-list">
    <li>
      <svg viewBox="0 0 24 24"><path d="M6.6 10.8a15.1 15.1 0 0 0 6.6 6.6l2.2-2.2a1 1 0 0 1 1-.25 11.4 11.4 0 0 0 3.6.6 1 1 0 0 1 1 1V20a1 1 0 0 1-1 1A17 17 0 0 1 3 4a1 1 0 0 1 1-1h3.5a1 1 0 0 1 1 1c0 1.25.2 2.45.6 3.6a1 1 0 0 1-.25 1z"/></svg>
      044-987 654 321
    </li>
    <li>
      <svg viewBox="0 0 24 24"><path d="M2 5h20v14H2z M2 5l10 8 10-8" /></svg>
      info@brookvane.com
    </li>
    <li>
      <svg viewBox="0 0 24 24"><path d="M12 2a10 10 0 1 0 0 20 10 10 0 0 0 0-20zm0 2c1 0 2.4 2 2.9 5H9.1C9.6 6 11 4 12 4zM4.3 11h4.6a18 18 0 0 0 0 2H4.3a8 8 0 0 1 0-2zm10.8 0h4.6a8 8 0 0 1 0 2h-4.6a18 18 0 0 0 0-2zM9.1 15h5.8c-.5 3-1.9 5-2.9 5s-2.4-2-2.9-5z"/></svg>
      www.brookvaneconsulting.com
    </li>
  </ul>

  <p class="tagline">CLARITY TO PLAN BETTER, LEAD BETTER, GROW BETTER</p>
</section>

<section class="card card-back" aria-label="Business card back">
  <div class="wordmark"><span class="wordmark-square"></span>Brookvane Consulting</div>
  <p class="back-url">www.brookvaneconsulting.com</p>
</section>

</body>
</html>
```